Stationery Design Project

I need a design that is simple, clean and modern, in square style, bold font.
The majority of the design needs to be White and Black with a splash of Red colour.
I would like a design for business cards and letter heads with the following information.
Name, Title, Phone, Fax, Email, Website and company ABN number

Target Market(s)

25 to 65 years old real estate clients

Industry/Entity Type

Business

Requirements
Must have
• All designs must incorporate Company Logo, Name, Title, Phone, Fax, Email, Website and company ABN number

```html
<!DOCTYPE html>
<html lang="en">
<head>
<meta charset="utf-8">
<title>Northgate Real Estate – Business Card</title>
<link href="https://fonts.googleapis.com/css2?family=Open+Sans:wght@400;600;700&display=swap" rel="stylesheet">
<style>
  :root {
    --bg: #e9e7e4;
    --card: #ffffff;
    --ink: #1a1a1a;
    --grey: #6b6b6b;
    --red: #d32f2f;
    --rule: #222222;
  }
  * { box-sizing: border-box; margin: 0; padding: 0; }
  html, body {
    width: 1200px; height: 402px; overflow: hidden;
    background: var(--bg);
    font-family: "Open Sans", Arial, sans-serif;
  }
  .canvas { position: relative; width: 1200px; height: 402px; }
  .card {
    position: absolute; top: 54px; width: 512px; height: 292px;
    background: var(--card);
    box-shadow: 0 2px 6px rgba(0,0,0,.18);
  }
  .card--front { left: 83px; }
  .card--back { left: 617px; }

  .brand-frame {
    position: absolute; left: 27px; top: 75px; width: 256px; height: 140px;
    border: 4px solid var(--ink); border-radius: 18px;
    display: flex; flex-direction: column; align-items: center; justify-content: center;
  }
  .brand-name {
    font-weight: 700; color: var(--ink); font-size: 27px; line-height: 1.15;
    text-transform: uppercase; text-align: center; letter-spacing: 1px;
    white-space: nowrap;
  }
  .divider {
    position: absolute; left: 317px; top: 44px; width: 1px; height: 209px;
    background: var(--rule);
  }
  .details { position: absolute; left: 341px; top: 62px; color: var(--grey); }
  .person { font-size: 16px; font-weight: 700; margin-bottom: 26px; }
  .person .title { font-size: 13px; font-weight: 400; }
  .contact-list { list-style: none; font-size: 13px; line-height: 17px; }
  .contact-list li { display: flex; align-items: center; gap: 6px; }
  .contact-list svg { width: 10px; height: 10px; flex: none; fill: var(--red); }
  .address { margin-top: 23px; font-size: 12.5px; line-height: 15px; }

  .back-brand {
    position: absolute; left: 90px; top: 128px; width: 170px;
    display: flex; align-items: center; gap: 8px;
  }
  .back-brand .brand-name { font-size: 24px; letter-spacing: .5px; }
  .back-brand .mark { width: 10px; height: 10px; background: var(--red); flex: none; }
  .website {
    position: absolute; left: 282px; top: 129px;
    font-size: 25px; line-height: 34px; color: var(--grey); letter-spacing: .3px;
    white-space: nowrap;
  }
  .website .accent { color: var(--red); }
</style>
</head>
<body>
<div class="canvas">
  <section class="card card--front">
    <div class="brand-frame">
      <div class="brand-name">Northgate<br>Real Estate</div>
    </div>
    <div class="divider"></div>
    <div class="details">
      <p class="person">Your name, <span class="title">Title</span></p>
      <ul class="contact-list">
        <li><svg viewBox="0 0 10 10" aria-hidden="true"><path d="M2 0.5l2 2-1 1.2c.6 1.3 1.6 2.3 2.9 2.9l1.2-1 2 2-1.3 1.7C4.5 9 1 5.5.3 1.8z"/></svg>123-456-7890</li>
        <li><svg viewBox="0 0 10 10" aria-hidden="true"><path d="M2.5 0h5a1 1 0 0 1 1 1v8a1 1 0 0 1-1 1h-5a1 1 0 0 1-1-1V1a1 1 0 0 1 1-1zm.6 1.2v6h3.8v-6zM5 8a.6.6 0 1 0 0 1.2A.6.6 0 0 0 5 8z"/></svg>123-456-7890</li>
        <li><svg viewBox="0 0 10 10" aria-hidden="true"><path d="M0 2h10v6H0z M0.6 2.4 5 5.6 9.4 2.4" stroke="#fff" stroke-width=".8"/></svg>info@mailbox.com</li>
        <li><svg viewBox="0 0 10 10" aria-hidden="true"><circle cx="5" cy="5" r="5"/><path d="M0 5h10M5 0c-2 2.5-2 7.5 0 10M5 0c2 2.5 2 7.5 0 10" stroke="#fff" stroke-width=".7" fill="none"/></svg>&nbsp;www.website.com</li>
      </ul>
      <p class="address">Street Name, City Name<br>State, City Zip Code</p>
    </div>
  </section>

  <section class="card card--back">
    <div class="back-brand">
      <span class="brand-name">Northgate</span>
      <span class="mark"></span>
    </div>
    <p class="website">www.<span class="accent">website</span>.com</p>
  </section>
</div>
</body>
</html>
```